Business Card Design

I need business cards designed for a new company i have started that makes cakes, particularly themed kids cakes with a really modern design and I would like to have my business cards reflect this. I have attached some photos of cakes I have made and would like some to be used.

Industry/Entity Type

Business

Contact Information for Business Card

Business Name: Tarts and Treats by Maren
Mobile: 0492 815 063
email: maren@tartsandtreatsbymaren.example.au
Instagram: instagram.com/tartsandtreatsbymaren/
Facebook: fb.me/tartsandtreatsbymaren

Colors
e667a6
b768aa
3276b5

Requirements
Must have
• Business Name: Tarts and Treats by Maren
• Mobile: 0492 815 063
• email: maren@tartsandtreatsbymaren.example.au
• Instagram: instagram.com/tartsandtreatsbymaren/
• Facebook: fb.me/tartsandtreatsbymaren
Nice to have
• 2 to 3 pictures of my cakes

```html
<!DOCTYPE html>
<html lang="en">
<head>
<meta charset="utf-8">
<title>Tarts and Treats by Maren — Business Card</title>
<link href="https://fonts.googleapis.com/css2?family=Lato:wght@300;400;700&display=swap" rel="stylesheet">
<style>
  :root {
    --backdrop: #ece8e4;
    --card-white: #ffffff;
    --berry: #b768aa;
    --berry-light: #c98bc0;
    --pink: #e667a6;
    --blue: #3276b5;
    --ink-light: #ffffff;
    --shadow: rgba(60, 40, 50, 0.18);
  }
  * { box-sizing: border-box; margin: 0; padding: 0; }
  html, body {
    width: 1200px; height: 843px; overflow: hidden;
    background: var(--backdrop);
    font-family: "Lato", sans-serif;
  }
  .canvas {
    position: relative; width: 1200px; height: 843px;
    display: flex; align-items: center; justify-content: center; gap: 40px;
  }
  .card {
    position: relative; width: 540px; height: 309px;
    background: var(--card-white);
    box-shadow: 0 12px 30px var(--shadow);
    overflow: hidden;
  }
  .card-front { display: flex; align-items: center; justify-content: center; }
  .brand-name {
    display: flex; align-items: center; gap: 10px;
    font-family: "Lato", sans-serif; font-weight: 400;
    color: var(--pink); letter-spacing: 0.3px; white-space: nowrap;
  }
  .brand-name .dot {
    width: 12px; height: 12px; border-radius: 50%; background: var(--pink);
    flex: none;
  }
  .card-front .brand-name { font-size: 30px; }
  .card-front .brand-name .dot { width: 14px; height: 14px; }

  .drip { position: absolute; inset: 0; width: 100%; height: 100%; }
  .contact {
    position: absolute; left: 34px; top: 48px;
    color: var(--ink-light);
  }
  .contact-name { font-size: 21px; font-weight: 300; letter-spacing: 1.5px; text-transform: uppercase; }
  .contact-title { font-size: 13px; font-weight: 300; margin-top: 4px; }
  .contact-list { list-style: none; margin-top: 24px; font-size: 12px; font-weight: 300; line-height: 1.7; }
  .contact-list .mobile { font-weight: 700; font-size: 13px; }
  .contact-list .handle { display: flex; align-items: center; gap: 7px; }
  .contact-list .icon {
    width: 11px; height: 11px; background: var(--ink-light); border-radius: 2px; flex: none;
  }
  .card-back .brand-name {
    position: absolute; right: 24px; bottom: 34px;
    font-size: 20px;
  }
</style>
</head>
<body>
<main class="canvas">
  <section class="card card-front" aria-label="Card front">
    <div class="brand-name"><span class="dot"></span>Tarts and Treats by Maren</div>
  </section>

  <section class="card card-back" aria-label="Card back">
    <svg class="drip" viewBox="0 0 540 309" preserveAspectRatio="none" aria-hidden="true">
      <defs>
        <linearGradient id="berryFill" x1="0" y1="0" x2="1" y2="0">
          <stop offset="0" stop-color="#b768aa"/>
          <stop offset="1" stop-color="#c98bc0"/>
        </linearGradient>
      </defs>
      <path fill="url(#berryFill)" d="M0 0 H310
        C340 0 345 35 330 60
        C312 90 350 105 372 82
        C398 55 432 72 416 108
        C402 138 352 132 346 158
        C340 182 372 192 366 212
        C358 236 320 230 300 218
        C282 206 250 222 244 248
        C238 280 222 309 200 309
        H0 Z"/>
    </svg>
    <div class="contact">
      <p class="contact-name">Maren Voss</p>
      <p class="contact-title">CEO/Founder</p>
      <ul class="contact-list">
        <li class="mobile">Mob: 0492 815 063</li>
        <li class="handle"><span class="icon"></span>tartsandtreatsbymaren</li>
        <li class="handle"><span class="icon"></span>tartsandtreatsbymaren</li>
        <li>maren@tartsandtreatsbymaren.example.au</li>
      </ul>
    </div>
    <div class="brand-name"><span class="dot"></span>Tarts and Treats by Maren</div>
  </section>
</main>
</body>
</html>
```